VTMB site redesign

Please redesign a home page with content provided. PSD only - no coding
Can use any images from Snapwelder.com

Please create a site design that more clearly illustrates the client's services and expertise. We are looking for a high-end design.

Any images used must be generic or of Dallas TX.

Fonts: Any
Colors: Match to logo
Look: Modern - Professional

Target Market(s)

medium-large business owners

Number of Pages Required

1 page

Font styles to use
Serif
Sans Serif

Requirements
Must have
• cohesive professional design
• high end look
• Match to logo

```html
<!DOCTYPE html>
<html lang="en">
<head>
<meta charset="utf-8">
<title>VTMB Commercial Realty Group</title>
<link href="https://fonts.googleapis.com/css2?family=Lora:wght@400;700&family=Lato:wght@400;700&display=swap" rel="stylesheet">
<style>
:root{
  --red:#d9312f;
  --red-dark:#b82523;
  --ink:#222222;
  --text:#555555;
  --muted:#888888;
  --light:#f4f4f4;
  --line:#dddddd;
  --dark:#333333;
  --white:#ffffff;
  --serif:'Lora', Georgia, serif;
  --sans:'Lato', Arial, sans-serif;
}
*{box-sizing:border-box;margin:0;padding:0}
html,body{width:1200px;height:3905px;overflow:hidden}
body{position:relative;font-family:var(--sans);color:var(--text);background:var(--white)}
.abs{position:absolute}
section,header,footer{position:absolute;left:0;width:1200px}
.ico{display:inline-block;vertical-align:middle}

/* header */
.site-header{top:0;height:148px;background:var(--white)}
.brand{left:120px;top:34px;display:flex;align-items:center;gap:12px}
.brand-mark{width:46px;height:46px;background:var(--red)}
.brand-name{font-family:var(--serif);font-weight:700;font-size:20px;line-height:1.15;color:var(--ink);letter-spacing:1px}
.brand-name small{display:block;font-size:12px;letter-spacing:2px;text-transform:uppercase}
.top-contact{right:120px;top:42px;display:flex;gap:40px;font-size:15px;color:var(--ink)}
.top-contact span{display:flex;align-items:center;gap:8px}
.top-contact .phone{color:var(--red)}
.main-nav{right:120px;top:84px;display:flex;align-items:center;gap:30px;font-size:15px;color:var(--ink)}
.main-nav .active{background:var(--red);color:var(--white);padding:5px 18px;border-radius:14px}

/* hero */
.hero{top:148px;height:662px;background:linear-gradient(180deg,#7a8796 0%,#a9b3bc 40%,#5b6066 75%,#2e2f33 100%)}
.hero-title{left:0;width:1200px;top:240px;text-align:center;font-family:var(--serif);font-weight:400;font-size:34px;line-height:44px;color:var(--white)}
.hero-sub{left:0;width:1200px;top:338px;text-align:center;font-size:15px;color:var(--white)}
.hero-btn{left:528px;top:372px;width:144px;height:42px;background:var(--red);color:var(--white);font-size:15px;display:flex;align-items:center;justify-content:center;border-radius:4px}
.hero-arrow{top:300px;width:30px;height:30px;border-radius:50%;background:var(--white);display:flex;align-items:center;justify-content:center}
.hero-dots{left:560px;top:615px;display:flex;gap:10px}
.hero-dots i{width:11px;height:11px;border-radius:50%;background:rgba(255,255,255,.55)}
.hero-dots i.on{background:var(--white)}

/* search */
.search-band{top:810px;height:166px;background:var(--light)}
.search-field{top:36px;height:42px;background:var(--white);border:1px solid var(--line);border-radius:4px;font-size:14px;color:var(--text);display:flex;align-items:center;justify-content:space-between;padding:0 16px}
.search-btn{left:945px;top:36px;width:135px;height:42px;background:var(--red);color:var(--white);border-radius:4px;font-size:15px;display:flex;align-items:center;justify-content:center;gap:10px}
.price-label{left:125px;top:92px;font-size:14px;color:var(--ink)}
.price-label b{color:var(--red);font-weight:400}
.adv-search{right:120px;top:92px;font-size:14px;color:var(--red);text-decoration:underline}
.range{left:135px;top:120px;width:935px;height:4px;background:var(--red)}
.range-knob{top:112px;width:18px;height:18px;border-radius:50%;background:var(--red)}

/* headings */
.section-title{left:0;width:1200px;text-align:center;font-family:var(--serif);font-weight:400;font-size:36px;color:var(--ink)}
.btn-red{width:170px;height:42px;background:var(--red);color:var(--white);border-radius:4px;font-size:15px;display:flex;align-items:center;justify-content:center}

/* properties */
.properties{top:976px;height:672px;background:var(--white)}
.filters{left:0;width:1200px;top:118px;display:flex;justify-content:center;gap:14px;font-size:16px;color:var(--ink)}
.filters .sep{color:var(--muted)}
.filters .on{color:var(--red)}
.slider-nav{right:120px;top:120px;display:flex;gap:8px}
.slider-nav i{width:22px;height:22px;border-radius:50%;display:flex;align-items:center;justify-content:center}
.card{top:177px;width:226px;height:318px;background:var(--white);box-shadow:0 2px 10px rgba(0,0,0,.1);padding:0 0 12px}
.card-img{height:148px;position:relative}
.badge{position:absolute;left:6px;top:6px;background:var(--red);color:var(--white);font-size:10px;padding:3px 7px}
.card-name{font-family:var(--serif);font-size:18px;color:var(--ink);padding:12px 8px 8px;border-bottom:1px solid var(--line);white-space:nowrap}
.card-row{display:flex;justify-content:space-between;font-size:13px;color:var(--text);padding:6px 8px;border-bottom:1px solid #eee}
.card-actions{display:flex;justify-content:space-between;padding:10px 8px 0}
.price{background:var(--red);color:var(--white);font-size:11px;border-radius:3px;padding:6px 10px;display:flex;gap:6px;align-items:center;min-width:115px}
.more{background:var(--dark);color:var(--white);font-size:11px;border-radius:3px;padding:6px 12px}

/* leasing */
.leasing{top:1648px;height:518px;background:var(--light)}
.leasing h2{left:120px;top:90px;width:500px;font-family:var(--serif);font-weight:400;font-size:31px;line-height:40px;color:var(--ink)}
.leasing .p1{left:120px;top:175px;width:490px;font-size:14px;line-height:22px}
.leasing .p2{left:120px;top:222px;width:490px;font-size:20px;line-height:30px;color:var(--ink)}
.leasing .p3{left:120px;top:292px;width:490px;font-size:14px;line-height:22px}
.leasing .btn-red{left:120px;top:385px}
.leasing-img{left:633px;top:96px;width:445px;height:331px;border-radius:6px;background:linear-gradient(135deg,#d7dadf 0%,#b8bcc2 45%,#c8353a 46%,#c8353a 60%,#e4e6e9 61%,#9fa4ab 100%)}

/* team */
.team{top:2166px;height:654px;background:var(--white)}
.member{top:164px;width:208px;text-align:center}
.member-photo{height:203px;border-radius:4px;background:linear-gradient(180deg,#8a6f66 0%,#5a4742 60%,#2b2526 100%)}
.member-photo.alt{background:linear-gradient(180deg,#e07a5a 0%,#c65a3e 60%,#3a2d2c 100%)}
.member-name{font-family:var(--serif);font-size:16px;color:var(--ink);margin-top:14px;height:30px;line-height:30px}
.member-name.hl{background:var(--red);color:var(--white)}
.member-role{font-size:15px;color:var(--text);margin-top:4px}
.member-social{display:flex;justify-content:center;gap:6px;margin-top:10px}
.member-social i{width:15px;height:15px;border-radius:50%;background:var(--ink)}
.pager{left:578px;top:508px;display:flex;gap:8px}
.pager i{width:8px;height:8px;border-radius:50%;background:var(--ink)}
.pager i.on{background:var(--red)}

/* blog */
.blog{top:2820px;height:560px;background:var(--light)}
.blog-sub{left:0;width:1200px;top:100px;text-align:center;font-size:14px;color:var(--ink)}
.post{top:122px;width:305px;height:325px;background:var(--white)}
.post-img{height:187px;position:relative}
.date{position:absolute;left:0;top:0;width:44px;height:48px;background:var(--red);color:var(--white);text-align:center;font-size:14px;line-height:18px;padding-top:6px}
.date small{display:block;font-size:10px}
.post-title{font-size:14px;font-weight:700;color:var(--ink);padding:12px 4px 6px}
.post-meta{display:flex;justify-content:space-between;font-size:13px;color:var(--text);padding:0 4px 8px}
.post-meta span{display:flex;align-items:center;gap:5px}
.post-text{font-size:14px;line-height:20px;color:var(--ink);padding:0 4px}
.post-more{font-size:14px;color:var(--ink);padding:10px 4px 0;letter-spacing:.5px}

/* footer */
.site-footer{top:3380px;height:525px;background:var(--dark);color:var(--white)}
.foot-title{font-family:var(--serif);font-weight:400;font-size:34px;color:var(--white)}
.foot-title::after{content:"";display:block;width:150px;height:4px;background:var(--red);margin-top:10px}
.field{left:120px;width:462px;height:40px;background:var(--white);border-radius:3px;color:var(--ink);font-size:14px;padding:10px 12px}
.send{left:120px;top:352px;width:156px;height:36px;background:var(--red);color:var(--white);border-radius:3px;font-size:15px;display:flex;align-items:center;justify-content:center}
.socials{left:400px;top:350px;display:flex;gap:12px}
.socials i{width:36px;height:36px;border-radius:50%;display:block}
.map{left:614px;top:130px;width:464px;height:255px;background:linear-gradient(135deg,#e8ecef 0%,#dfe5ea 50%,#cfd9e3 100%);border-radius:2px}
.copy{left:120px;top:406px;font-size:14px;line-height:22px;font-weight:700}
.address{right:122px;top:406px;text-align:right;font-size:14px;line-height:22px;font-weight:700}
</style>
</head>
<body>

<header class="site-header">
  <div class="abs brand">
    <span class="brand-mark"></span>
    <span class="brand-name">VTMB<small>Vantmore Commercial Realty Group</small></span>
  </div>
  <div class="abs top-contact">
    <span><svg width="16" height="16" viewBox="0 0 24 24"><path d="M6.6 10.8a15 15 0 0 0 6.6 6.6l2.2-2.2c.3-.3.7-.4 1-.2 1.1.4 2.3.6 3.6.6.6 0 1 .4 1 1V20c0 .6-.4 1-1 1A17 17 0 0 1 3 4c0-.6.4-1 1-1h3.5c.6 0 1 .4 1 1 0 1.3.2 2.5.6 3.6.1.3 0 .7-.2 1z" fill="#222"/></svg>info@vtmbusa.com</span>
    <span class="phone"><svg width="16" height="16" viewBox="0 0 24 24"><path d="M6.6 10.8a15 15 0 0 0 6.6 6.6l2.2-2.2c.3-.3.7-.4 1-.2 1.1.4 2.3.6 3.6.6.6 0 1 .4 1 1V20c0 .6-.4 1-1 1A17 17 0 0 1 3 4c0-.6.4-1 1-1h3.5c.6 0 1 .4 1 1 0 1.3.2 2.5.6 3.6.1.3 0 .7-.2 1z" fill="#d9312f"/></svg>214-555-0148</span>
  </div>
  <nav class="abs main-nav">
    <span class="active">Home</span><span>Services</span><span>About VTMB</span><span>Blog</span><span>Contact us</span><span>Market News</span>
    <svg width="14" height="14" viewBox="0 0 24 24"><circle cx="10" cy="10" r="7" stroke="#222" stroke-width="3" fill="none"/><path d="M15 15l7 7" stroke="#222" stroke-width="3"/></svg>
  </nav>
</header>

<section class="hero" role="img" aria-label="Photograph of a downtown city skyline with tall towers under a cloudy sky">
  <h1 class="abs hero-title">The Best Commercial Tenant Reps<br>in Dallas TX!</h1>
  <p class="abs hero-sub">Let Us Handle Your Commercial Real Estate Lease Negotiations!</p>
  <div class="abs hero-btn">Read More</div>
  <div class="abs hero-arrow" style="left:56px"><svg width="10" height="10" viewBox="0 0 10 10"><path d="M7 1L3 5l4 4" stroke="#222" stroke-width="2" fill="none"/></svg></div>
  <div class="abs hero-arrow" style="right:44px"><svg width="10" height="10" viewBox="0 0 10 10"><path d="M3 1l4 4-4 4" stroke="#222" stroke-width="2" fill="none"/></svg></div>
  <div class="abs hero-dots"><i></i><i class="on"></i><i></i><i class="on"></i></div>
</section>

<section class="search-band">
  <div class="abs search-field" style="left:120px;width:255px">Location <svg class="ico" width="8" height="12" viewBox="0 0 8 12"><path d="M1 4l3-3 3 3M1 8l3 3 3-3" stroke="#555" stroke-width="1.5" fill="none"/></svg></div>
  <div class="abs search-field" style="left:392px;width:205px">Category <svg class="ico" width="8" height="12" viewBox="0 0 8 12"><path d="M1 4l3-3 3 3M1 8l3 3 3-3" stroke="#555" stroke-width="1.5" fill="none"/></svg></div>
  <div class="abs search-field" style="left:606px;width:182px">Type <svg class="ico" width="8" height="12" viewBox="0 0 8 12"><path d="M1 4l3-3 3 3M1 8l3 3 3-3" stroke="#555" stroke-width="1.5" fill="none"/></svg></div>
  <div class="abs search-field" style="left:797px;width:134px">Status <svg class="ico" width="8" height="12" viewBox="0 0 8 12"><path d="M1 4l3-3 3 3M1 8l3 3 3-3" stroke="#555" stroke-width="1.5" fill="none"/></svg></div>
  <div class="abs search-btn"><svg width="13" height="13" viewBox="0 0 24 24"><circle cx="10" cy="10" r="7" stroke="#fff" stroke-width="3" fill="none"/><path d="M15 15l7 7" stroke="#fff" stroke-width="3"/></svg>Search</div>
  <div class="abs price-label">Price $ <b>0000 - 10000</b></div>
  <div class="abs adv-search">Advance Search</div>
  <div class="abs range"></div>
  <div class="abs range-knob" style="left:126px"></div>
  <div class="abs range-knob" style="left:1060px"></div>
</section>

<section class="properties">
  <h2 class="abs section-title" style="top:40px">Properties</h2>
  <div class="abs filters"><span class="on">All</span><span class="sep">|</span><span>House</span><span class="sep">|</span><span>Offices</span><span class="sep">|</span><span>Appartment</span><span class="sep">|</span><span>Resdential</span><span class="sep">|</span><span>Other</span></div>
  <div class="abs slider-nav">
    <i style="background:#333"><svg width="8" height="8" viewBox="0 0 10 10"><path d="M7 1L3 5l4 4" stroke="#fff" stroke-width="2" fill="none"/></svg></i>
    <i style="background:var(--red)"><svg width="8" height="8" viewBox="0 0 10 10"><path d="M3 1l4 4-4 4" stroke="#fff" stroke-width="2" fill="none"/></svg></i>
  </div>

  <article class="abs card" style="left:118px">
    <div class="card-img" role="img" aria-label="Photograph of an open green field under a cloudy sky" style="background:linear-gradient(180deg,#9aa6ae 0%,#b9bfbf 50%,#6f7a4f 70%,#59653c 100%)"><span class="badge">Sale</span></div>
    <div class="card-name">Speedway</div>
    <div class="card-row"><span>Village</span></div>
    <div class="card-row"><span>Squre Footage</span><span>450 $</span></div>
    <div class="card-row"><span>Type</span><span>House</span></div>
    <div class="card-actions"><span class="price"><svg width="11" height="11" viewBox="0 0 24 24"><path d="M2 3h4l3 12h11l3-9H7" stroke="#fff" stroke-width="2.5" fill="none"/><circle cx="10" cy="20" r="2" fill="#fff"/><circle cx="18" cy="20" r="2" fill="#fff"/></svg>$30,730,085.40</span><span class="more">Read More</span></div>
  </article>
  <article class="abs card" style="left:365px">
    <div class="card-img" role="img" aria-label="Photograph of a furnished office lobby" style="background:linear-gradient(180deg,#5b4a3e 0%,#8a7258 55%,#b7a58a 100%)"><span class="badge">Sale</span></div>
    <div class="card-name">Parkway Office</div>
    <div class="card-row"><span>Flat</span></div>
    <div class="card-row"><span>Squre Footage</span><span>450 $</span></div>
    <div class="card-row"><span>Type</span><span>House</span></div>
    <div class="card-actions"><span class="price"><svg width="11" height="11" viewBox="0 0 24 24"><path d="M2 3h4l3 12h11l3-9H7" stroke="#fff" stroke-width="2.5" fill="none"/><circle cx="10" cy="20" r="2" fill="#fff"/><circle cx="18" cy="20" r="2" fill="#fff"/></svg>$19.50</span><span class="more">Read More</span></div>
  </article>
  <article class="abs card" style="left:612px">
    <div class="card-img" role="img" aria-label="Photograph of a bright conference room" style="background:linear-gradient(180deg,#e6e8ea 0%,#c5c9cc 55%,#7d8185 100%)"><span class="badge">Sale</span></div>
    <div class="card-name">Turtle Creek</div>
    <div class="card-row"><span>Office Space Sublease</span></div>
    <div class="card-row"><span>Squre Footage</span><span>150 $</span></div>
    <div class="card-row"><span>Type</span><span>Office</span></div>
    <div class="card-actions"><span class="price"><svg width="11" height="11" viewBox="0 0 24 24"><path d="M2 3h4l3 12h11l3-9H7" stroke="#fff" stroke-width="2.5" fill="none"/><circle cx="10" cy="20" r="2" fill="#fff"/><circle cx="18" cy="20" r="2" fill="#fff"/></svg>$32.86</span><span class="more">Read More</span></div>
  </article>
  <article class="abs card" style="left:860px">
    <div class="card-img" role="img" aria-label="Photograph of a white low-rise studio building" style="background:linear-gradient(180deg,#dfe3e6 0%,#f1efe9 50%,#9b7b6a 100%)"><span class="badge">Sale</span></div>
    <div class="card-name">Media Production Studio</div>
    <div class="card-row"><span>Bedroom</span></div>
    <div class="card-row"><span>Squre Footage</span><span>450 $</span></div>
    <div class="card-row"><span>Type</span><span>Production Studio</span></div>
    <div class="card-actions"><span class="price"><svg width="11" height="11" viewBox="0 0 24 24"><path d="M2 3h4l3 12h11l3-9H7" stroke="#fff" stroke-width="2.5" fill="none"/><circle cx="10" cy="20" r="2" fill="#fff"/><circle cx="18" cy="20" r="2" fill="#fff"/></svg>$1,903,535.00</span><span class="more">Read More</span></div>
  </article>

  <div class="abs btn-red" style="left:515px;top:550px">View More</div>
</section>

<section class="leasing">
  <h2 class="abs">Professional Office &amp; Warehouse Leasing</h2>
  <p class="abs p1">Fast-track your search with tenant reps that only serve you, and specialize in the DFW area.</p>
  <p class="abs p2">Fast-track your search with tenant reps that only serve you, and specialize in the DFW area.</p>
  <p class="abs p3">Save time by trusting VTMB year after year to find the right location for you. Once we've worked together, we know what you need, and you can keep your budget details private</p>
  <div class="abs btn-red">Read More</div>
  <div class="abs leasing-img" role="img" aria-label="Photograph of a leasing sign beside a calculator, glasses and a pen on paperwork"></div>
</section>

<section class="team">
  <h2 class="abs section-title" style="top:74px">Meet The Team</h2>
  <div class="abs member" style="left:120px">
    <div class="member-photo" role="img" aria-label="Portrait photograph of the founder and president"></div>
    <div class="member-name">Graham T. Whitfield</div>
    <div class="member-role">Founder and President</div>
    <div class="member-social"><i></i><i></i><i></i><i></i></div>
  </div>
  <div class="abs member" style="left:362px">
    <div class="member-photo" role="img" aria-label="Portrait photograph of the senior director"></div>
    <div class="member-name hl">Owen Castell-Reed</div>
    <div class="member-role">Senior Director</div>
    <div class="member-social"><i></i><i></i><i></i><i></i></div>
  </div>
  <div class="abs member" style="left:610px">
    <div class="member-photo alt" role="img" aria-label="Portrait photograph of the associate"></div>
    <div class="member-name">Daniel Joseph Brandt</div>
    <div class="member-role">Associate</div>
    <div class="member-social"><i></i><i></i><i></i><i></i></div>
  </div>
  <div class="abs member" style="left:872px">
    <div class="member-photo" role="img" aria-label="Portrait photograph of the founder and president"></div>
    <div class="member-name">Graham T. Whitfield</div>
    <div class="member-role">Founder and President</div>
    <div class="member-social"><i></i><i></i><i></i><i></i></div>
  </div>
  <div class="abs pager"><i class="on"></i><i></i><i></i></div>
  <div class="abs btn-red" style="left:518px;top:546px">View More</div>
</section>

<section class="blog">
  <h2 class="abs section-title" style="top:46px">Our Blog</h2>
  <p class="abs blog-sub">Lorem Ipsum is simply dummy text.</p>
  <article class="abs post" style="left:120px">
    <div class="post-img" role="img" aria-label="Photograph of an open-plan office with desks and windows" style="background:linear-gradient(180deg,#e9eef2 0%,#c9d2d9 55%,#8b949b 100%)"><span class="date">06<small>May</small></span></div>
    <div class="post-title">Do You Need Office Space?</div>
    <div class="post-meta"><span><svg width="11" height="11" viewBox="0 0 12 12"><rect x="1" y="2" width="10" height="9" fill="none" stroke="#d9312f" stroke-width="1.5"/><path d="M1 5h10" stroke="#d9312f" stroke-width="1.5"/></svg>May 04, 2018</span><span><svg width="12" height="11" viewBox="0 0 12 11"><path d="M1 1h10v7H5l-3 2V8H1z" fill="none" stroke="#555" stroke-width="1.2"/></svg>20 &nbsp; <svg width="11" height="10" viewBox="0 0 12 11"><path d="M6 10L1.5 5.5A2.6 2.6 0 0 1 6 2.3a2.6 2.6 0 0 1 4.5 3.2z" fill="none" stroke="#555" stroke-width="1.2"/></svg>13</span></div>
    <p class="post-text">Lorem Ipsum is simply dummy text of the printing matter and typesetting industry.</p>
    <div class="post-more">Read More&#8594;</div>
  </article>
  <article class="abs post" style="left:449px">
    <div class="post-img" role="img" aria-label="Photograph of a shared office lounge with people working" style="background:linear-gradient(180deg,#d8c8b0 0%,#b49a7a 55%,#6e5a47 100%)"><span class="date">07<small>May</small></span></div>
    <div class="post-title">Shared Building Amenities</div>
    <div class="post-meta"><span><svg width="11" height="11" viewBox="0 0 12 12"><rect x="1" y="2" width="10" height="9" fill="none" stroke="#d9312f" stroke-width="1.5"/><path d="M1 5h10" stroke="#d9312f" stroke-width="1.5"/></svg>May 03, 2018</span><span><svg width="12" height="11" viewBox="0 0 12 11"><path d="M1 1h10v7H5l-3 2V8H1z" fill="none" stroke="#555" stroke-width="1.2"/></svg>20 &nbsp; <svg width="11" height="10" viewBox="0 0 12 11"><path d="M6 10L1.5 5.5A2.6 2.6 0 0 1 6 2.3a2.6 2.6 0 0 1 4.5 3.2z" fill="none" stroke="#555" stroke-width="1.2"/></svg>13</span></div>
    <p class="post-text">Lorem Ipsum is simply dummy text of the printing matter and typesetting industry.</p>
    <div class="post-more">Read More&#8594;</div>
  </article>
  <article class="abs post" style="left:778px">
    <div class="post-img" role="img" aria-label="Photograph of a commercial lease document with banknotes" style="background:linear-gradient(135deg,#a9743f 0%,#e8e2d6 40%,#f4f1ea 70%,#8e6a45 100%)"><span class="date">06<small>May</small></span></div>
    <div class="post-title">Entering Into A Commercial Lease?</div>
    <div class="post-meta"><span><svg width="11" height="11" viewBox="0 0 12 12"><rect x="1" y="2" width="10" height="9" fill="none" stroke="#d9312f" stroke-width="1.5"/><path d="M1 5h10" stroke="#d9312f" stroke-width="1.5"/></svg>May 02, 2018</span><span><svg width="12" height="11" viewBox="0 0 12 11"><path d="M1 1h10v7H5l-3 2V8H1z" fill="none" stroke="#555" stroke-width="1.2"/></svg>20 &nbsp; <svg width="11" height="10" viewBox="0 0 12 11"><path d="M6 10L1.5 5.5A2.6 2.6 0 0 1 6 2.3a2.6 2.6 0 0 1 4.5 3.2z" fill="none" stroke="#555" stroke-width="1.2"/></svg>13</span></div>
    <p class="post-text">Lorem Ipsum is simply dummy text of the printing matter and typesetting industry.</p>
    <div class="post-more">Read More&#8594;</div>
  </article>
  <div class="abs btn-red" style="left:518px;top:478px">View More</div>
</section>

<footer class="site-footer">
  <h2 class="abs foot-title" style="left:120px;top:52px">Contact us</h2>
  <h2 class="abs foot-title" style="left:614px;top:52px">Map</h2>
  <div class="abs field" style="top:150px">Name</div>
  <div class="abs field" style="top:207px">Phone</div>
  <div class="abs field" style="top:252px;height:76px">Message</div>
  <div class="abs send">Send</div>
  <div class="abs socials"><i style="background:#3b5b98"></i><i style="background:#2a6fb0"></i><i style="background:#d9312f"></i><i style="background:#3aa3e3"></i></div>
  <div class="abs map" role="img" aria-label="Street map of the office neighborhood with a location marker"></div>
  <p class="abs copy">All Rights Reserved.<br>Copyright 2018 VTMB Vantmore Commercial Realty Group.</p>
  <p class="abs address">4120 Cedar Row Avenue, Suite 312, Dallas, TX 75298<br>Tel: 214-555-0190 | Fax: 214-555-0191</p>
</footer>

</body>
</html>
```